TL - business card

Tallow Partners is an insurance brokerage firm, inovative, proactive, vigorous, which aims to become the leader of the insurance brokers in Anfrica. We should like to get some designs which should be avoided also in Gray / Metallic for the Administration and Orange / Blue for the Managers (ike in the picture sent). The Blue / Green logo is not the correct one, but the source of the file. Please adjust the color accordingly for the business cards. 1 / Orange / Blue 2 / Gray / Metallic We want something classic but which is transmitted strenght, inovation, modernity and most of all, rapidity. We want something start-up like, very punchy and catching eye remaining profesional at the same time. Name: Dorian Whitlock Function: Managing Director Address: N ° 17/18 Rua Veloso - R / C 2B Direita - Bairro Mutamba - Luanda Tel: (+244) 947 582 316 Email: dorian.whitlock@tallow-p.example Website: www.tallow-p. example We want classic in the front and creative, colorfull at the back. The cards will be printed in relief, with very high quality of paper.
Insurance Broker
Colors
Designer to choose colors to be used in the design.

```html
<!DOCTYPE html>
<html lang="en">
<head>
<meta charset="utf-8">
<title>Tallow Partners – Business Card</title>
<link rel="stylesheet" href="https://fonts.googleapis.com/css2?family=Bitter:wght@700&family=Open+Sans:wght@400;600;700;800&display=swap">
<style>
  :root {
    --orange: #f0901c;
    --blue: #22a3dc;
    --charcoal: #38383b;
    --ink: #1f1f1f;
    --paper: #f7f7f7;
    --stage: #e6e4e1;
    --white: #ffffff;
  }
  * { box-sizing: border-box; margin: 0; padding: 0; }
  html, body { width: 1200px; height: 900px; overflow: hidden; }
  body {
    background: var(--stage);
    font-family: "Open Sans", Arial, sans-serif;
    color: var(--ink);
    position: relative;
  }
  .card {
    position: absolute;
    left: 300px;
    width: 600px;
    height: 343px;
    border-radius: 4px;
    box-shadow: 0 6px 18px rgba(0,0,0,0.18);
    overflow: hidden;
  }
  /* Front */
  .card--front { top: 60px; background: var(--paper); }
  .brand {
    position: absolute;
    left: 40px; top: 108px;
    display: flex; align-items: center; gap: 14px;
  }
  .brand__dot {
    width: 46px; height: 46px; border-radius: 50%;
    background: var(--orange);
  }
  .brand__name {
    font-weight: 800; font-size: 30px; color: var(--orange);
    letter-spacing: 0.5px; text-transform: uppercase; line-height: 1;
  }
  .person {
    position: absolute; right: 40px; top: 34px;
    display: flex; align-items: center; gap: 12px;
  }
  .person__icon { width: 36px; height: 36px; }
  .person__name {
    font-family: "Bitter", Georgia, serif; font-weight: 700;
    font-size: 22px; color: var(--blue); line-height: 1.1;
  }
  .person__role { font-size: 13px; color: var(--orange); text-align: right; }
  .rule {
    position: absolute; left: 30px; right: 30px; top: 176px;
    height: 2px; background: var(--orange);
  }
  .contact {
    position: absolute; right: 40px; top: 196px;
    list-style: none; font-size: 13px; line-height: 1;
  }
  .contact li { display: flex; align-items: center; gap: 8px; margin-bottom: 9px; }
  .contact svg { width: 14px; height: 14px; flex: none; }
  .address {
    position: absolute; left: 40px; top: 208px;
    display: flex; gap: 12px; font-size: 16px; line-height: 1.35;
  }
  .address svg { width: 20px; height: 26px; flex: none; margin-top: 2px; }
  /* Back */
  .card--back { top: 470px; background: var(--charcoal); }
  .back-mark {
    position: absolute; left: 0; right: 0; top: 78px;
    display: flex; flex-direction: column; align-items: center; gap: 22px;
  }
  .back-mark__dot { width: 96px; height: 96px; border-radius: 50%; background: var(--orange); }
  .back-mark__name {
    font-weight: 800; font-size: 46px; color: var(--orange);
    text-transform: uppercase; letter-spacing: 1px; line-height: 1;
  }
  .back-web {
    position: absolute; left: 0; right: 0; bottom: 34px;
    text-align: center; color: var(--white);
    font-weight: 700; font-size: 20px; letter-spacing: 10px;
  }
</style>
</head>
<body>

<section class="card card--front" aria-label="Business card front">
  <div class="person">
    <svg class="person__icon" viewBox="0 0 36 36" aria-hidden="true">
      <circle cx="18" cy="18" r="18" fill="var(--charcoal)"/>
      <circle cx="18" cy="14" r="6" fill="var(--white)"/>
      <path d="M7 30c2-6 7-8 11-8s9 2 11 8z" fill="var(--white)"/>
    </svg>
    <div>
      <p class="person__name">Dorian Whitlock</p>
      <p class="person__role">Managing Director</p>
    </div>
  </div>

  <div class="brand">
    <span class="brand__dot"></span>
    <span class="brand__name">Tallow Partners</span>
  </div>

  <div class="rule"></div>

  <div class="address">
    <svg viewBox="0 0 20 26" aria-hidden="true"><path d="M10 1a8 8 0 0 0-8 8c0 6 8 15 8 15s8-9 8-15a8 8 0 0 0-8-8z" fill="var(--orange)"/><circle cx="10" cy="9" r="3.2" fill="var(--paper)"/></svg>
    <p>N ° 17/18 Rua Veloso<br>- R / C 2B Direita -<br>Bairro Mutamba - Luanda</p>
  </div>

  <ul class="contact">
    <li>
      <svg viewBox="0 0 14 14" aria-hidden="true"><path d="M3 1l2 3-1.3 1.3a7 7 0 0 0 5 5L10 9l3 2-1 2.5C6 13 1 8 .5 2z" fill="var(--orange)"/></svg>
      (+244) 947 582 316
    </li>
    <li>
      <svg viewBox="0 0 14 14" aria-hidden="true"><rect x="1" y="3" width="12" height="8" fill="var(--orange)"/><path d="M1 3l6 5 6-5" stroke="var(--white)" stroke-width="1.2" fill="none"/></svg>
      dorian.whitlock@tallow-p.example
    </li>
    <li>
      <svg viewBox="0 0 14 14" aria-hidden="true"><circle cx="7" cy="7" r="6" fill="none" stroke="var(--orange)" stroke-width="1.5"/><path d="M1 7h12M7 1c-3 3-3 9 0 12M7 1c3 3 3 9 0 12" stroke="var(--orange)" fill="none"/></svg>
      www.tallow-p. example
    </li>
  </ul>
</section>

<section class="card card--back" aria-label="Business card back">
  <div class="back-mark">
    <span class="back-mark__dot"></span>
    <span class="back-mark__name">Tallow Partners</span>
  </div>
  <p class="back-web">www.tallow-p. example</p>
</section>

</body>
</html>
```